Business Card Design Project

Keep it simple , using logo and colors that compliment. Logo on one side with complimentary back ground color. Other side, personal info with possible complimentary design/colors

Target Market(s)

we are a non for profit that will be seeking donations . Both monetary and in kind

Industry/Entity Type

Business

Font styles to use
Sans Serif

Colors

Designer to choose colors to be used in the design.

```html
<!DOCTYPE html>
<html lang="en">
<head>
<meta charset="utf-8">
<title>Spark Real Good – Business Card</title>
<link href="https://fonts.googleapis.com/css2?family=Arimo:wght@400;700&display=swap" rel="stylesheet">
<style>
  :root {
    --backdrop: #2a2a2a;
    --card: #f7f7f7;
    --navy: #1e2548;
    --navy-text: #2a3a8c;
    --yellow: #e5d800;
    --ink: #111111;
    --muted: #333333;
  }
  * { margin: 0; padding: 0; box-sizing: border-box; }
  html, body {
    width: 1200px; height: 997px; overflow: hidden;
    background: var(--backdrop);
    font-family: "Arimo", Arial, sans-serif;
  }
  .card {
    position: absolute; left: 250px;
    width: 700px; height: 400px;
    background: var(--card);
    overflow: hidden;
    box-shadow: 0 10px 30px rgba(0,0,0,.45);
  }
  .card--front { top: 60px; }
  .card--back  { top: 530px; }
  .card__bands { position: absolute; inset: 0; }

  .brand {
    position: absolute; display: flex; align-items: center;
    color: var(--navy); font-weight: 400; white-space: nowrap; line-height: 1;
  }
  .card--front .brand {
    left: 50%; top: 50%; transform: translate(-50%, -60%);
    font-size: 40px; gap: 14px;
  }
  .card--back .brand {
    left: 40px; top: 50%; transform: translateY(-60%);
    font-size: 24px; gap: 10px;
  }
  .brand__mark { display: block; background: var(--navy); flex: none; }
  .card--front .brand__mark { width: 22px; height: 22px; }
  .card--back  .brand__mark { width: 14px; height: 14px; }

  .divider {
    position: absolute; left: 350px; top: 40px; width: 4px; height: 290px;
    background: linear-gradient(to bottom, rgba(30,37,72,0), var(--navy) 45%, rgba(30,37,72,0));
  }
  .person { position: absolute; left: 385px; top: 58px; }
  .person__name { color: var(--navy-text); font-weight: 700; font-size: 19px; letter-spacing: .3px; }
  .person__title { color: var(--ink); font-weight: 700; font-size: 13px; margin-top: 3px; letter-spacing: .3px; }

  .contact { position: absolute; left: 385px; top: 160px; list-style: none; }
  .contact__item {
    display: flex; align-items: center; gap: 10px;
    font-size: 15px; color: var(--muted); height: 27px; white-space: nowrap;
  }
  .contact__icon { width: 14px; height: 14px; flex: none; }
</style>
</head>
<body>

<section class="card card--front" aria-label="Card front">
  <svg class="card__bands" viewBox="0 0 700 400" aria-hidden="true">
    <path d="M0 382 H470 V400 H0 Z" fill="var(--navy)"/>
    <path d="M450 400 V376 Q450 356 474 356 H700 V400 Z" fill="var(--yellow)"/>
  </svg>
  <div class="brand"><span class="brand__mark"></span><span>Spark Real Good</span></div>
</section>

<section class="card card--back" aria-label="Card back">
  <svg class="card__bands" viewBox="0 0 700 400" aria-hidden="true">
    <path d="M0 382 H500 V400 H0 Z" fill="var(--navy)"/>
    <path d="M480 400 V372 Q480 350 506 350 H700 V400 Z" fill="var(--yellow)"/>
  </svg>

  <div class="brand"><span class="brand__mark"></span><span>Spark Real Good</span></div>

  <div class="divider"></div>

  <div class="person">
    <p class="person__name">JONAH WHITCOMBE</p>
    <p class="person__title">MANAGING DIRECTOR</p>
  </div>

  <ul class="contact">
    <li class="contact__item">
      <svg class="contact__icon" viewBox="0 0 14 14" aria-hidden="true"><path d="M3 1 L5 4 L4 5.5 Q5.5 8.5 8.5 10 L10 9 L13 11 L11.5 13 Q5 12 1 3 Z" fill="var(--navy)"/></svg>
      <span>+61 400 217 964</span>
    </li>
    <li class="contact__item">
      <svg class="contact__icon" viewBox="0 0 14 14" aria-hidden="true"><rect x="0.5" y="2.5" width="13" height="9" fill="var(--navy)"/><path d="M1 3 L7 8 L13 3" stroke="#fff" stroke-width="1.2" fill="none"/></svg>
      <span>jonah@brightlantern.org.au</span>
    </li>
    <li class="contact__item">
      <svg class="contact__icon" viewBox="0 0 14 14" aria-hidden="true"><g fill="none" stroke="var(--navy)" stroke-width="1.6"><rect x="1" y="6" width="7" height="4" rx="2" transform="rotate(-45 4.5 8)"/><rect x="6" y="4" width="7" height="4" rx="2" transform="rotate(-45 9.5 6)"/></g></svg>
      <span>www.brightlantern.org.au</span>
    </li>
    <li class="contact__item">
      <svg class="contact__icon" viewBox="0 0 14 14" aria-hidden="true"><circle cx="7" cy="7" r="5" fill="var(--navy)"/></svg>
      <span>social: @brightlantern</span>
    </li>
  </ul>
</section>

</body>
</html>
```